Global (re)insurance broker needs a business card design

We need a classic business card for our company that is headquartered in SG, with offices in Malaysia and Dubai. We specialise in insurance and reinsurance broking and consultancy for our global clients.

```html
<!DOCTYPE html>
<html lang="en">
<head>
<meta charset="utf-8">
<title>Valmore business card</title>
<link rel="stylesheet" href="https://fonts.googleapis.com/css2?family=Open+Sans:wght@400;600;700&display=swap">
<style>
  :root {
    --backdrop: #2b2b2e;
    --card-dark: #1f1e23;
    --brand-blue: #2447a6;
    --brand-blue-deep: #1c3a92;
    --brand-blue-light: #2f55bf;
    --mint: #b8d4b0;
    --ink-light: #eceef2;
  }
  * { box-sizing: border-box; margin: 0; padding: 0; }
  html, body { width: 1200px; height: 780px; overflow: hidden; }
  body {
    background: var(--backdrop);
    font-family: "Open Sans", Arial, sans-serif;
    position: relative;
  }
  .card {
    position: absolute;
    top: 235px;
    width: 540px;
    height: 310px;
    border-radius: 3px;
    overflow: hidden;
    box-shadow: 0 10px 24px rgba(0,0,0,.35);
  }
  .card--front { left: 40px; background: var(--card-dark); }
  .card--back { left: 620px; background: var(--brand-blue); }

  .holder { position: absolute; left: 0; top: 26px; padding-left: 30px; }
  .holder__bar {
    position: absolute; left: 0; top: 4px;
    width: 8px; height: 34px; background: var(--brand-blue);
  }
  .holder__name { font-size: 30px; font-weight: 600; line-height: 1.2; }
  .holder__first { color: var(--brand-blue-light); }
  .holder__last { color: var(--mint); }
  .holder__title { font-size: 13px; color: var(--ink-light); margin-top: 0; }

  .wordmark { position: absolute; font-weight: 700; letter-spacing: 2px; line-height: 1; }
  .card--front .wordmark { right: 30px; top: 112px; font-size: 60px; color: var(--mint); }

  .contacts { position: absolute; left: 30px; top: 140px; list-style: none; }
  .contacts li {
    display: flex; align-items: center; gap: 8px;
    font-size: 13px; color: var(--ink-light); line-height: 21px;
  }
  .contacts svg { width: 12px; height: 12px; flex: none; }

  .address {
    position: absolute; right: 30px; bottom: 26px;
    font-size: 15px; color: var(--ink-light); line-height: 1.45; font-style: normal;
  }

  .back-pattern {
    position: absolute; inset: 0;
    background: linear-gradient(100deg, var(--brand-blue-deep) 0%, var(--brand-blue) 55%, #3a5fc4 100%);
  }
  .card--back .wordmark {
    left: 0; right: 0; top: 50%; transform: translateY(-50%);
    text-align: center; font-size: 64px; color: #ffffff;
  }
</style>
</head>
<body>
  <section class="card card--front">
    <div class="holder">
      <span class="holder__bar"></span>
      <h1 class="holder__name"><span class="holder__first">Mira</span> <span class="holder__last">Lind</span></h1>
      <p class="holder__title">Chief Operating Officer</p>
    </div>

    <ul class="contacts">
      <li>
        <svg viewBox="0 0 12 12" aria-hidden="true"><rect x="3" y="0.5" width="6" height="11" rx="1" fill="none" stroke="#eceef2"/><line x1="5" y1="9.5" x2="7" y2="9.5" stroke="#eceef2"/></svg>
        +65 6100 2048
      </li>
      <li>
        <svg viewBox="0 0 12 12" aria-hidden="true"><circle cx="6" cy="6" r="5.5" fill="#2f55bf"/><ellipse cx="6" cy="6" rx="2.4" ry="5.5" fill="none" stroke="#1f1e23" stroke-width=".8"/><line x1="0.5" y1="6" x2="11.5" y2="6" stroke="#1f1e23" stroke-width=".8"/></svg>
        www.valmore.com
      </li>
      <li>
        <svg viewBox="0 0 12 12" aria-hidden="true"><rect x="0.5" y="2.5" width="11" height="8" fill="none" stroke="#b8d4b0"/><polyline points="0.5,2.5 6,7 11.5,2.5" fill="none" stroke="#b8d4b0"/></svg>
        mira@valmore.com
      </li>
    </ul>

    <div class="wordmark">VALMORE</div>

    <address class="address">28 Harbour Lane, Meridian<br>Tower #08-04, Singapore 018910</address>
  </section>

  <section class="card card--back">
    <div class="back-pattern" role="img" aria-label="Faint repeated company name pattern across a blue field"></div>
    <div class="wordmark">VALMORE</div>
  </section>
</body>
</html>
```